uk based ecommerce website requires fresh look ,high quality look and feel

we are a web based company selling eco friendly ground reinforcement grids to diy and construction sectors
our existing website is www.pondermeshpaths.co.uk ,

we have already updated the logo so that is the branding sorted .so we need a ecommerce website that is very much up-to date in design and layout and which has content management system for ease of use so that we can add products and information as required.

Use current logo as reference for colour scheme.
www.pondermeshpaths.co.uk

The current website has 6 pages accessible through the navigation bar, I would now like 5 pages, removing the need for the Trade Enquiries page possibly have it with along with contact us.

Target Market(s)

construction industry , diy end users,
retail market, landscapers, gardeners

Industry/Entity Type

Construction

Font styles to use
Other font styles liked:
• logo font prometo

Colors
f78f20
9bcb3c

Requirements
Must have
• logo colours and logo design in website with cms responsive design for tablet and mobile devices
• expect content to work flawlessly and look great across all devices
• HTML 5 custom design with coding as required
• must have good experiance in ecommerce website design
• eye catching, high quality look and feel and very user friedly ,very up-to date.
Nice to have
• picture slider show
• explain in writing what exactly i am getting in my ecommerce website
Should not have
• plain , basic design , old fashion looking ,cheap look

```html
<!DOCTYPE html>
<html lang="en">
<head>
<meta charset="utf-8">
<title>Pondermesh Ground Solutions</title>
<link href="https://fonts.googleapis.com/css2?family=Ubuntu:wght@400;500&family=Open+Sans:wght@400;600&display=swap" rel="stylesheet">
<style>
:root{
  --orange:#f78f20;
  --orange-light:#fba54a;
  --green:#9bcb3c;
  --ink:#333333;
  --muted:#666666;
  --panel:#f6f6f6;
  --line:#e2e2e2;
  --footer:#2d2d2d;
  --footer-base:#222222;
  --white:#ffffff;
}
*{box-sizing:border-box;margin:0;padding:0}
html,body{width:690px;height:1200px;overflow:hidden;background:var(--white)}
body{position:relative;font-family:"Open Sans",sans-serif;color:var(--ink)}
.abs{position:absolute}
h1,h2,h3,h4,.brand,.nav a,.btn{font-family:"Ubuntu",sans-serif}

.topbar{left:0;top:0;width:690px;height:28px;background:linear-gradient(var(--orange-light),var(--orange));color:var(--white);font-size:7px;letter-spacing:.4px}
.topbar .phones{left:76px;top:10px;display:flex;gap:4px;align-items:center}
.topbar .mail{right:76px;top:10px;display:flex;gap:5px;align-items:center}

.header{left:0;top:28px;width:690px;height:73px;background:var(--white);box-shadow:0 1px 3px rgba(0,0,0,.12);z-index:2}
.brand{left:76px;top:20px;display:flex;align-items:center;gap:6px;color:var(--orange);font-weight:500;font-size:14px;line-height:1.05;letter-spacing:.3px}
.brand .mark{width:22px;height:22px;background:var(--green)}
.account{right:76px;top:13px;display:flex;gap:4px}
.account span{background:var(--green);color:var(--white);font-size:6.5px;letter-spacing:.5px;padding:6px 10px;border-radius:2px}
.nav{right:76px;top:49px;display:flex;gap:22px;font-size:6.6px;letter-spacing:.4px}
.nav a{color:var(--ink);text-decoration:none}
.nav a.active{color:var(--orange)}

.hero{left:0;top:101px;width:690px;height:213px;background:linear-gradient(160deg,#6f9a3a 0%,#88a955 18%,#a0656a 34%,#a66a72 60%,#8e5c60 100%)}
.hero h1{left:76px;top:112px;font-size:23px;font-weight:500;letter-spacing:1.5px;color:#333}
.hero p{left:76px;top:150px;font-family:"Ubuntu",sans-serif;font-size:11px;font-weight:500;letter-spacing:.8px;color:#3a3a3a}
.dots{left:76px;top:176px;display:flex;gap:5px}
.dots i{width:8px;height:8px;border-radius:50%;background:rgba(255,255,255,.55)}
.dots i:first-child{background:var(--white)}

.title{width:690px;left:0;text-align:center;font-size:18.5px;font-weight:500;letter-spacing:1.2px;color:var(--ink)}
.title span{color:var(--orange)}
.welcome-text{left:78px;top:370px;width:534px;text-align:center;font-size:6.6px;line-height:11px;letter-spacing:.35px;color:var(--muted)}
.btn{display:inline-flex;align-items:center;justify-content:center;gap:4px;height:22px;padding:0 11px;border-radius:11px;background:var(--orange);color:var(--white);font-size:6.5px;letter-spacing:.5px;box-shadow:0 2px 3px rgba(0,0,0,.15)}
.btn svg{width:6px;height:6px}
.btn.light{background:var(--white);color:var(--ink)}

.products{left:0;top:476px;width:690px;height:247px;background:var(--panel);border-top:1px solid var(--line);border-bottom:1px solid var(--line)}
.arrow{width:10px;height:12px}
.cat{top:75px;width:260px;height:133px;display:flex;box-shadow:0 6px 6px -3px rgba(0,0,0,.3)}
.cat .photo{width:138px;height:133px}
.cat .body{flex:1;padding:16px 10px 0;color:var(--white)}
.cat h3{font-size:11.5px;font-weight:500;letter-spacing:.7px;line-height:13px;margin-bottom:8px}
.cat p{font-size:5.8px;line-height:11px;letter-spacing:.4px;margin-bottom:8px}

.feat{top:797px;width:123px;height:197px;border:1px solid var(--line);text-align:center}
.feat .photo{height:81px}
.feat h4{margin-top:11px;height:34px;font-size:9px;font-weight:400;letter-spacing:.6px;line-height:13px;color:var(--green)}
.feat .price{font-family:"Ubuntu",sans-serif;font-size:9px;letter-spacing:.5px;color:var(--green);margin-bottom:13px}

.footer{left:0;top:1023px;width:690px;height:141px;background:var(--footer);color:var(--white)}
.footer .brand{left:76px;top:24px;color:#777777}
.footer .brand .mark{background:#777777;border-radius:50%}
.social{left:76px;top:87px;display:flex;gap:3px}
.social i{width:19px;height:19px;border:1px solid var(--white);border-radius:50%}
.footer h4{font-size:9px;font-weight:500;letter-spacing:.6px}
.links{left:247px;top:22px}
.links ul{list-style:none;margin-top:8px;font-size:6px;line-height:12px}
.news{left:349px;top:22px}
.news p{font-size:5.8px;margin:9px 0 9px}
.news .field{width:113px;height:20px;background:#555555;font-size:5.6px;padding:7px 7px}
.news .btn{margin-top:11px;height:15px;font-size:5.6px;padding:0 8px;box-shadow:none}
.contact{left:502px;top:22px}
.contact ul{list-style:none;margin-top:9px;font-size:6px}
.contact li{display:flex;gap:7px;align-items:flex-start;margin-bottom:7px;line-height:8px}
.contact svg{width:7px;height:7px;flex:none}
.base{left:0;top:1164px;width:690px;height:36px;background:var(--footer-base);color:var(--white);font-size:5.8px;text-align:center;padding-top:15px}
</style>
</head>
<body>

<div class="abs topbar">
  <div class="abs phones">
    <svg width="7" height="7" viewBox="0 0 10 10"><path d="M2 0l2 2.5-1.2 1.3c.7 1.4 1.8 2.5 3.2 3.2L7.5 6 10 8l-1.5 2C4 10 0 6 0 1.5z" fill="#fff"/></svg>
    <span>&nbsp;0138-555-0142 &nbsp;|&nbsp; 0845-555-0190</span>
  </div>
  <div class="abs mail">
    <svg width="8" height="6" viewBox="0 0 10 7"><rect width="10" height="7" fill="#fff"/><path d="M0 0l5 4 5-4" stroke="#f78f20" fill="none"/></svg>
    <span>sales@pondermeshpaths.co.uk</span>
  </div>
</div>

<header class="abs header">
  <div class="abs brand"><i class="mark"></i><span>PONDERMESH<br>GROUND SOLUTIONS</span></div>
  <div class="abs account"><span>LOGIN</span><span>REGISTER</span></div>
  <nav class="abs nav">
    <a class="active">HOME</a><a>SHOP</a><a>ABOUT US</a><a>GROUND SOLUTIONS</a><a>PONDERMESH</a><a>CONTACT US</a>
  </nav>
</header>

<section class="abs hero">
  <div class="abs" style="inset:0" role="img" aria-label="Photo of a curved red block-paved driveway beside a grass lawn"></div>
  <h1 class="abs">PONDERMESH SYSTEM</h1>
  <p class="abs">GRAVELGRID SYSTEM FOR DRIVEWAYS &amp; PATHWAYS</p>
  <div class="abs dots"><i></i><i></i><i></i></div>
</section>

<section>
  <h2 class="abs title" style="top:340px">WELCOME TO <span>PONDERMESH</span></h2>
  <p class="abs welcome-text">PONDERMESH is a family run company that specialises in stabilisation grid systems for gravel and grass surfaces. Our main focus is to provide Quality products at an affordable price and which meets the requirements of our customers. We supply a permeable paving system that keeps the traditional look of a gravel driveway, but gives it the more advanced and ecological approach of a contained gravel system</p>
  <div class="abs" style="left:310px;top:417px">
    <span class="btn"><svg viewBox="0 0 10 10"><circle cx="5" cy="5" r="5" fill="#fff"/><path d="M4 3l2 2-2 2" stroke="#f78f20" fill="none" stroke-width="1.4"/></svg>MORE INFO</span>
  </div>
</section>

<section class="abs products">
  <h2 class="abs title" style="top:26px">OUR <span>PRODUCTS</span></h2>
  <svg class="abs arrow" style="left:53px;top:124px" viewBox="0 0 10 12"><path d="M7 1L2 6l5 5" stroke="#222" stroke-width="1.6" fill="none"/></svg>
  <svg class="abs arrow" style="left:627px;top:124px" viewBox="0 0 10 12"><path d="M3 1l5 5-5 5" stroke="#222" stroke-width="1.6" fill="none"/></svg>

  <article class="abs cat" style="left:76px">
    <div class="photo" role="img" aria-label="Photo of black geotextile membrane laid over a garden plot" style="background:linear-gradient(#6f6a55,#55544e 40%,#4a4a4a)"></div>
    <div class="body" style="background:var(--orange)">
      <h3>GEOTEXTILE<br>MEMBRANES</h3>
      <p>These geotextiles also have a water filtration characteristic. The pore size of the geotextile is small enough to</p>
      <span class="btn light"><svg viewBox="0 0 10 10"><circle cx="5" cy="5" r="5" fill="#333"/><path d="M4 3l2 2-2 2" stroke="#fff" fill="none" stroke-width="1.4"/></svg>MORE INFO</span>
    </div>
  </article>

  <article class="abs cat" style="left:352px">
    <div class="photo" role="img" aria-label="Photo of dark gravel filling a black hexagonal grid" style="background:linear-gradient(#5a5a5a,#3a3a3a)"></div>
    <div class="body" style="background:var(--green)">
      <h3>LIGHT DOMESTIC<br>DRIVEWAYS</h3>
      <p>These geotextiles also have a water filtration characteristic. The pore size of the geotextile is small enough to</p>
      <span class="btn light"><svg viewBox="0 0 10 10"><circle cx="5" cy="5" r="5" fill="#333"/><path d="M4 3l2 2-2 2" stroke="#fff" fill="none" stroke-width="1.4"/></svg>MORE INFO</span>
    </div>
  </article>
</section>

<section>
  <h2 class="abs title" style="top:750px">FEATURED <span>PRODUCTS</span></h2>
  <svg class="abs arrow" style="left:53px;top:895px" viewBox="0 0 10 12"><path d="M7 1L2 6l5 5" stroke="#222" stroke-width="1.6" fill="none"/></svg>
  <svg class="abs arrow" style="left:627px;top:895px" viewBox="0 0 10 12"><path d="M3 1l5 5-5 5" stroke="#222" stroke-width="1.6" fill="none"/></svg>

  <article class="abs feat" style="left:76px">
    <div class="photo" role="img" aria-label="Photo of a bicycle wheel on a gravel-filled grid" style="background:linear-gradient(#5c5c5c,#8a8a88)"></div>
    <h4>PONDERMESH 25<br>SYSTEM</h4>
    <div class="price">£ 11.00 EACH</div>
    <span class="btn"><svg viewBox="0 0 10 10"><circle cx="5" cy="5" r="5" fill="#fff"/><path d="M4 3l2 2-2 2" stroke="#f78f20" fill="none" stroke-width="1.4"/></svg>MORE INFO</span>
  </article>
  <article class="abs feat" style="left:214px">
    <div class="photo" role="img" aria-label="Photo of a white paving grid part-filled with pea gravel" style="background:linear-gradient(#9c8f78,#b8ad98)"></div>
    <h4>TERRALOCK 40<br>PAVING SYSTEM</h4>
    <div class="price">£ 11.00 EACH</div>
    <span class="btn"><svg viewBox="0 0 10 10"><circle cx="5" cy="5" r="5" fill="#fff"/><path d="M4 3l2 2-2 2" stroke="#f78f20" fill="none" stroke-width="1.4"/></svg>MORE INFO</span>
  </article>
  <article class="abs feat" style="left:352px">
    <div class="photo" role="img" aria-label="Photo of a van wheel on a pale gravel driveway" style="background:linear-gradient(90deg,#c9bfae,#8a8a88 60%,#3e3e3e)"></div>
    <h4>HEAVY DOMESTIC<br>DRIVEWAYS</h4>
    <div class="price">£ 11.00 EACH</div>
    <span class="btn"><svg viewBox="0 0 10 10"><circle cx="5" cy="5" r="5" fill="#fff"/><path d="M4 3l2 2-2 2" stroke="#f78f20" fill="none" stroke-width="1.4"/></svg>MORE INFO</span>
  </article>
  <article class="abs feat" style="left:490px">
    <div class="photo" role="img" aria-label="Photo of a red block-paved path beside garden planting" style="background:linear-gradient(135deg,#6b7a5a,#7d5a5e 45%,#8a6668)"></div>
    <h4>PARKING AND<br>PATHWAY SYSTEM</h4>
    <div class="price">£ 11.00 EACH</div>
    <span class="btn"><svg viewBox="0 0 10 10"><circle cx="5" cy="5" r="5" fill="#fff"/><path d="M4 3l2 2-2 2" stroke="#f78f20" fill="none" stroke-width="1.4"/></svg>MORE INFO</span>
  </article>
</section>

<footer class="abs footer">
  <div class="abs brand"><i class="mark"></i><span>PONDERMESH<br>GROUND SOLUTIONS</span></div>
  <div class="abs social"><i></i><i></i><i></i><i></i><i></i></div>

  <div class="abs links">
    <h4>QUICK LINKS</h4>
    <ul><li>Home</li><li>Shop</li><li>About Us</li><li>Ground Solutions</li><li>Pondermesh</li><li>Contact Us</li></ul>
  </div>

  <div class="abs news">
    <h4>NEWSLETTER</h4>
    <p>Sign Up for Our Newsletter &amp; Promotion</p>
    <div class="field">Enter Your email Id</div>
    <span class="btn">SUBSCRIBE</span>
  </div>

  <div class="abs contact">
    <h4>CONTACT US</h4>
    <ul>
      <li><svg viewBox="0 0 10 10"><path d="M0 3q5-4 10 0v2H7V3.5H3V5H0zM2 5h6l1 5H1z" fill="#fff"/></svg>0138-555-0142</li>
      <li><svg viewBox="0 0 10 10"><rect x="2" y="0" width="6" height="3" fill="#fff"/><rect x="0" y="3" width="10" height="4" fill="#fff"/><rect x="2" y="7" width="6" height="3" fill="#fff"/></svg>0845-555-0190</li>
      <li><svg viewBox="0 0 10 7"><rect width="10" height="7" fill="#fff"/><path d="M0 0l5 4 5-4" stroke="#2d2d2d" fill="none"/></svg><u>sales@pondermeshpaths.co.uk</u></li>
      <li><svg viewBox="0 0 10 10"><path d="M5 0a3.5 3.5 0 0 1 3.5 3.5C8.5 6 5 10 5 10S1.5 6 1.5 3.5A3.5 3.5 0 0 1 5 0z" fill="#fff"/><circle cx="5" cy="3.5" r="1.3" fill="#2d2d2d"/></svg><span>#2868 Lorem ipsum dolor sit amet,<br>consectetur adipiscing</span></li>
    </ul>
  </div>
</footer>

<div class="abs base">Copyright © 2016 pondermeshpaths.co.uk</div>

</body>
</html>
```